body therapist

I need to offer my services as a massage therapist at home, acclimating customer space aroma candles with music and everything else to bring comfort. 8 offer rituals like this: relaxing ritual, purifying ritual, ritual breast, facial and body cleansing ritual organic, ritual man, ritual feet, slimming ritual. Naraja handling colors, seawater, green, lavender

Target Market(s)

men and women, tired, stressed, looking for something new

Font styles to use
Decorative
Script

Colors
f37122
0493ce
abd037

Requirements
Must have
• detailing each massage
Nice to have
• simple and elegant

```html
<!DOCTYPE html>
<html lang="es">
<head>
<meta charset="utf-8">
<title>Alborada Spa – Masajes</title>
<link rel="stylesheet" href="https://fonts.googleapis.com/css2?family=Allura&family=Didact+Gothic&family=Cutive&display=swap">
<style>
  :root {
    --backdrop: #f2f2f2;
    --page: #ffffff;
    --lime: #abd037;
    --lime-deep: #a3cc35;
    --orchid: #c65bcc;
    --ink: #555555;
    --ink-soft: #6a6a6a;
    --tab: #e2e2e2;
    --panel-top: #d6d7d9;
    --panel-bottom: #ffffff;
    --panel-edge: #b9b9b9;
    --photo-warm: #f0a460;
    --photo-light: #f7d9b2;
    --photo-deep: #c9683a;
  }
  * { box-sizing: border-box; margin: 0; padding: 0; }
  html, body { width: 1000px; height: 1200px; overflow: hidden; }
  body { background: var(--backdrop); position: relative; font-family: "Didact Gothic", sans-serif; }

  .page {
    position: absolute; left: 107px; top: 30px; width: 793px; height: 1130px;
    background: var(--page); overflow: hidden;
  }
  .page-tab {
    position: absolute; left: 350px; top: 0; width: 92px; height: 58px;
    background: var(--tab); border-radius: 0 0 46px 46px;
    text-align: center; font-size: 22px; line-height: 70px; color: #333;
  }
  .brand-title {
    position: absolute; left: 0; width: 100%; top: 62px; text-align: center;
    font-family: "Allura", cursive; font-weight: 400; font-size: 92px; color: var(--lime); line-height: 1;
  }
  .intro {
    position: absolute; left: 36px; width: 726px; top: 176px;
    font-size: 17.5px; line-height: 22px; color: var(--ink-soft);
    letter-spacing: 0.5px;
  }
  .intro-line { display: block; white-space: nowrap; }
  .intro-line--full { text-align: justify; text-align-last: justify; white-space: normal; }
  .lime-band {
    position: absolute; left: 21px; top: 370px; width: 744px; height: 520px;
    background: var(--lime-deep);
  }
  .photo { position: absolute; left: 0; top: 0; width: 793px; height: 1130px; }

  .menu-panel {
    position: absolute; left: 402px; top: 303px; width: 306px; height: 755px;
    background: linear-gradient(to bottom, var(--panel-top), var(--panel-bottom) 70%);
    border: 1px solid var(--panel-edge);
    overflow: hidden;
  }
  .menu-title {
    position: absolute; left: 16px; top: 40px; width: 280px;
    font-family: "Cutive", monospace; font-weight: 400; font-size: 43px; letter-spacing: 0;
    color: var(--orchid); line-height: 1; white-space: nowrap;
  }
  .menu-list { position: absolute; left: 16px; top: 133px; width: 280px; list-style: none; }
  .menu-list li {
    position: relative; padding-left: 27px; font-size: 24px; line-height: 31px;
    color: var(--ink); margin-bottom: 32px;
  }
  .menu-list li::before {
    content: ""; position: absolute; left: 0; top: 9px; width: 13px; height: 13px;
    background: var(--orchid);
  }
  .duration-tag {
    position: absolute; left: 535px; top: 942px; width: 258px; height: 78px;
    background: var(--lime-deep); color: #fff; font-size: 26px;
    line-height: 80px; padding-left: 10px; white-space: nowrap;
  }
</style>
</head>
<body>
  <main class="page">
    <div class="page-tab">3</div>
    <h1 class="brand-title">Alborada Spa</h1>
    <p class="intro">
      <span class="intro-line">Un espacio para tu CUERPO, MENTE Y ESPIRITU…</span>
      <span class="intro-line intro-line--full">ALBORADA es una empresa dedicada a brindar bienestar al ser sin salir de</span>
      <span class="intro-line intro-line--full">casa; transformando tu espacio con innovadoras técnicas de masajes,</span>
      <span class="intro-line">terapias y rituales para así llegar al máximo nivel de relajación del zen.</span>
    </p>

    <div class="lime-band"></div>

    <svg class="photo" viewBox="0 0 793 1130" role="img" aria-label="Fotografía de una mujer relajada recibiendo un masaje en la espalda sobre una toalla blanca">
      <defs>
        <linearGradient id="warmTone" x1="0" y1="0" x2="1" y2="1">
          <stop offset="0" stop-color="#f7d9b2"/>
          <stop offset="0.45" stop-color="#f0a460"/>
          <stop offset="1" stop-color="#c9683a"/>
        </linearGradient>
      </defs>
      <path d="M0,460 Q420,430 793,930 L793,1130 L0,1130 Z" fill="url(#warmTone)"/>
    </svg>

    <section class="menu-panel">
      <h2 class="menu-title">MASAJES</h2>
      <ul class="menu-list">
        <li>MASAJE ZEN CON</li>
        <li>PIEDRAS SABAY</li>
        <li>MASAJE AROMÁTICO</li>
        <li>MASAJE A CUATRO MANOS</li>
        <li>MASAJE RELAJANTE</li>
        <li>MASAJE REDUCTOR</li>
      </ul>
    </section>

    <div class="duration-tag">DE 60-90 MINUTES</div>
  </main>
</body>
</html>
```